Start-up braucht modernes/hochwertiges Getränkeetikett
Zielgruppe
Wir sind ein modernes, nachhaltiges Start-up, welches eine neue Getränkekategorie auf den Markt bringt. Ein sogenanntes Elektrolyt-Getränk mit dem Namen FLUXO4. Es ist abgefüllt in eine 500 ml Flasche und enthält Magnesium, Kalzium, Kalium, und Natrium. Diese Stoffe (Elektrolyte) dienen der körperlichen Hydrierung. Zu Dehydrierung kann es durch Hitze, Alkohol, Sport oder Krankheit kommen. Krankheit liegt bei uns allerdings nicht im Fokus. In unserer Zielgruppe befinden sich hauptsächlich Personen im Alter von 18 - 29 Jahren.
Die Geschmacksrichtung ist Zitrone-Limette.
Aufgabenstellung
Das Etikett soll:
- MODERN, SCHLICHT und HOCHWERTIG sein, so dass es im Supermarkt hervorsticht
- erkenntlich machen, dass die Stoffe Magnesium, Natrium, Kalzium und Kalium enthalten sind
- sich farblich deutlich von der Farbe des Inhalts (weiß) abheben. (Vorzugsweise mit einem hellen Blau, türkis)
- für unsere junge Zielgruppe ansprechend sein
- ebenfalls auf die Geschmacksrichtung (Zitrone-Limette) hinweisen, und zwar so, dass wenn man eine weitere Geschmacksrichtung auf den Markt bringen möchte, diese leicht angepasst werden kann.
- nicht nach einem Energydrink oder einem typischen Sportgetränk aussehen
- unter dem Namen den Slogan 'Elektrolyt-Getränk' stehen haben
-Das Etikett ist nicht dursichtig sondern besteht aus Papier
Der Name sowie das Logo können selbstverständlich farblich verändert werden. Bei dem Logo können auch größere Änderungen vollzogen werden.
Bitte beachten Sie die unten zu stehenden Regler um sich einen guten Überblick über unsere Vorstellungen zu verschaffen. Die Platzierung des EAN-Code ist für ihr Design irrelevat .
Bei Unklarheiten gerne nachfragen!

```html
<!DOCTYPE html>
<html lang="de">
<head>
<meta charset="utf-8">
<title>FLUXO4 Etikett</title>
<link rel="stylesheet" href="https://fonts.googleapis.com/css2?family=Poppins:wght@700&family=Quicksand:wght@300&family=Montserrat:wght@800&family=Oswald:wght@500&display=swap">
<style>
  :root {
    --stage: #d9dadc;
    --label-pale: #bde9f5;
    --panel-start: #5ac5e0;
    --panel-end: #a9d9e4;
    --stripe-top: #7b7fb8;
    --stripe-pink: #f5a8b2;
    --stripe-orange: #f3bb8c;
    --stripe-bottom: #f7d6e3;
    --brand-white: #f1f3f4;
    --lemon: #8cc63f;
    --lime-yellow: #e8e24a;
  }
  html, body {
    margin: 0;
    width: 667px;
    height: 1200px;
    overflow: hidden;
    background: var(--stage);
  }
  .label {
    position: absolute;
    left: 12px;
    top: 98px;
    width: 642px;
    height: 1003px;
    display: block;
  }
  .brand-name { font-family: "Poppins", sans-serif; font-weight: 700; fill: var(--brand-white); }
  .tagline { font-family: "Quicksand", sans-serif; font-weight: 300; fill: var(--brand-white); }
  .flavor { font-family: "Montserrat", sans-serif; font-weight: 800; }
  .flavor-lemon { fill: var(--lemon); }
  .flavor-lime { fill: var(--lime-yellow); }
  .mineral { font-family: "Oswald", sans-serif; font-weight: 500; fill: #ffffff; font-size: 24px; }
  .brand-ring { fill: none; stroke: var(--brand-white); stroke-width: 3; }
</style>
</head>
<body>
<svg class="label" viewBox="0 0 730 1140" xmlns="http://www.w3.org/2000/svg" aria-label="FLUXO4 Elektrolyt-Getränk Etikett">
  <defs>
    <linearGradient id="flavor-stripe" x1="0" y1="0" x2="0" y2="1">
      <stop offset="0" stop-color="var(--stripe-top)"/>
      <stop offset="0.38" stop-color="var(--stripe-pink)"/>
      <stop offset="0.68" stop-color="var(--stripe-orange)"/>
      <stop offset="1" stop-color="var(--stripe-bottom)"/>
    </linearGradient>
    <linearGradient id="brand-panel" x1="0" y1="0" x2="1" y2="0">
      <stop offset="0" stop-color="var(--panel-start)"/>
      <stop offset="1" stop-color="var(--panel-end)"/>
    </linearGradient>
  </defs>

  <rect class="label-base" width="730" height="1140" fill="var(--label-pale)"/>
  <rect class="brand-panel" x="283" width="447" height="1140" fill="url(#brand-panel)"/>
  <rect class="flavor-stripe" x="188" width="95" height="1140" fill="url(#flavor-stripe)"/>

  <g class="flavor-name">
    <text class="flavor flavor-lemon" font-size="22" transform="translate(234,145) rotate(-90)" textLength="95">ZITRONE</text>
    <text class="flavor flavor-lime" font-size="22" transform="translate(259,145) rotate(-90)" textLength="95">LIMETTE</text>
  </g>

  <text class="brand-name" font-size="228" transform="translate(485,855) rotate(-90)" textLength="810" lengthAdjust="spacingAndGlyphs">FLUXO4</text>
  <text class="tagline" font-size="44" transform="translate(550,500) rotate(-90)" textLength="455">Elektrolyt-Getränk</text>

  <circle class="brand-ring" cx="400" cy="1055" r="84"/>

  <g class="mineral-list" text-anchor="end">
    <text class="mineral" x="138" y="751">Magnesium</text>
    <text class="mineral" x="138" y="858">Natrium</text>
    <text class="mineral" x="138" y="965">Kalcium</text>
    <text class="mineral" x="138" y="1073">Kalium</text>
  </g>
</svg>
</body>
</html>
```